I am looking for a modern, clean and neat design for a reflexology and well being business. The business name is Gralo Tund (this is an old Latin word for wellbeing). The colours I would like are purple, white and grey. I am open to suggestions for pictures such as healing or working hands, a pair of feet, images that represent my business that you may think of....... or maybe you think no images at all would be best? My tag line is: "Relax, Renew, Revive" or "Find you balance......... Relax, Renew, Revive" I can decide which I want so I would like to see what both would look like. I would like space on the back to write the client's appointment date and time (more than once)

```html
<!DOCTYPE html>
<html lang="en">
<head>
<meta charset="utf-8">
<title>Gralo Tund — Business Card</title>
<link rel="stylesheet" href="https://fonts.googleapis.com/css2?family=Open+Sans:wght@300;400;600;700&display=swap">
<style>
  :root {
    --bg: #e9e9ec;
    --card: #ffffff;
    --lavender: #a3b9e0;
    --ink: #3f3f42;
    --grey: #4d4d50;
    --soft-grey: #8a8a8e;
    --rule: #5a5a5e;
  }
  * { box-sizing: border-box; margin: 0; padding: 0; }
  html, body {
    width: 1200px; height: 900px; overflow: hidden;
    background: var(--bg);
    font-family: "Open Sans", sans-serif;
    color: var(--ink);
  }
  .canvas { position: relative; width: 1200px; height: 900px; }
  .card {
    position: absolute; width: 660px; height: 380px;
    background: var(--card); border-radius: 26px; overflow: hidden;
    box-shadow: 0 6px 18px rgba(0,0,0,0.12);
  }
  .card--back { left: 270px; top: 50px; }
  .card--front { left: 270px; top: 470px; }

  .brand { position: absolute; display: flex; align-items: center; gap: 14px; }
  .brand__dot { width: 46px; height: 46px; border-radius: 50%; background: var(--lavender); }
  .brand__name { font-weight: 300; font-size: 32px; letter-spacing: 1px; color: var(--soft-grey); text-transform: uppercase; white-space: nowrap; }

  /* back */
  .tagline { position: absolute; right: 48px; top: 40px; font-size: 13px; font-weight: 400; letter-spacing: 0.5px; color: var(--ink); }
  .card--back .brand { left: 50px; top: 120px; }
  .appointment { position: absolute; left: 50px; top: 232px; width: 520px; }
  .appointment__title { font-size: 21px; color: var(--lavender); font-weight: 400; margin-bottom: 8px; }
  .appointment__row { display: flex; align-items: flex-end; height: 32px; font-size: 15px; }
  .appointment__label { width: 58px; }
  .appointment__line { flex: 1; border-bottom: 1px solid var(--rule); margin-bottom: 4px; }

  /* front */
  .card--front .brand { left: 46px; top: 130px; }
  .person { position: absolute; right: 40px; top: 74px; text-align: right; }
  .person__name { font-size: 28px; font-weight: 700; letter-spacing: 1.5px; color: var(--ink); text-transform: uppercase; line-height: 1; white-space: nowrap; }
  .person__role { font-size: 12px; letter-spacing: 1px; text-transform: uppercase; color: var(--ink); margin-top: 2px; }
  .person__rule { position: absolute; right: 110px; top: 108px; width: 200px; border-top: 1.5px solid var(--lavender); }
  .contact { position: absolute; left: 46px; top: 262px; padding-top: 10px; border-top: 1.5px solid var(--lavender); width: 290px; }
  .contact__item { display: flex; align-items: center; gap: 10px; font-size: 15px; line-height: 21px; color: var(--ink); }
  .contact__icon { width: 11px; height: 11px; flex: none; }
  .band { position: absolute; left: 0; bottom: 0; width: 660px; height: 34px; }
</style>
</head>
<body>
<main class="canvas">

  <section class="card card--back" aria-label="Appointment side">
    <p class="tagline">RELAX, RENEW, REVIVE</p>
    <div class="brand">
      <span class="brand__dot"></span>
      <span class="brand__name">Gralo Tund</span>
    </div>
    <div class="appointment">
      <h2 class="appointment__title">Appointment:</h2>
      <div class="appointment__row"><span class="appointment__label">Name:</span><span class="appointment__line"></span></div>
      <div class="appointment__row"><span class="appointment__label">Time:</span><span class="appointment__line"></span></div>
      <div class="appointment__row"><span class="appointment__label">Date:</span><span class="appointment__line"></span></div>
    </div>
  </section>

  <section class="card card--front" aria-label="Contact side">
    <div class="brand">
      <span class="brand__dot"></span>
      <span class="brand__name">Gralo Tund</span>
    </div>
    <div class="person">
      <p class="person__name">Mara Vell</p>
      <p class="person__role">Director</p>
    </div>
    <span class="person__rule"></span>
    <div class="contact">
      <p class="contact__item">
        <svg class="contact__icon" viewBox="0 0 12 12"><path d="M2 1h2.5l1 3-1.5 1a6 6 0 0 0 3 3l1-1.5 3 1V10a1 1 0 0 1-1 1A9 9 0 0 1 1 2a1 1 0 0 1 1-1z" fill="var(--lavender)"/></svg>
        +330 5182-7394
      </p>
      <p class="contact__item">
        <svg class="contact__icon" viewBox="0 0 12 12"><rect x="0.5" y="2" width="11" height="8" rx="1" fill="none" stroke="var(--lavender)" stroke-width="1.2"/><path d="M1 2.5l5 4 5-4" fill="none" stroke="var(--lavender)" stroke-width="1.2"/></svg>
        info@gralotund.com
      </p>
      <p class="contact__item">
        <svg class="contact__icon" viewBox="0 0 12 12"><circle cx="6" cy="6" r="5" fill="none" stroke="var(--lavender)" stroke-width="1.2"/><path d="M1 6h10M6 1c2 2.5 2 7.5 0 10M6 1c-2 2.5-2 7.5 0 10" fill="none" stroke="var(--lavender)" stroke-width="1"/></svg>
        www.gralotund.com
      </p>
    </div>
    <svg class="band" viewBox="0 0 660 34" preserveAspectRatio="none">
      <polygon points="0,28 352,28 368,8 372,8 356,34 0,34" fill="var(--grey)"/>
      <polygon points="372,8 660,8 660,34 356,34" fill="var(--lavender)"/>
    </svg>
  </section>

</main>
</body>
</html>
```